Business card for Luxury Portable Restroom Trailer company

We are a Luxury Portable Restroom Trailer Company Called FALCRIDGE HIRES. Based in Orange County California. We provide portable restroom trailers for events, such as, Weddings, Concerts, Charity events, Sporting events, Tournaments, Corporate events, ect. We rent and Sell the Luxury restrooms. Our colors are white, grey, and Orange. As you will see in the logo we uploaded.
There are 2 people in the company so the names and titles will change for the 3 people but card will remain the same. Here is the information for each Person: Dwight Penner CFO 555 318-0476
next Person: Leon Marchetti VP 555 318-0476
Next Person: Owen Marchetti CEO 555 318-0476
Information to include on the card: Luxury Restroom Trailers Rental and Sales. Weddings, Concerts, Charity, Sporting and Corp. Events.

```html
<!DOCTYPE html>
<html lang="en">
<head>
<meta charset="utf-8">
<title>Falcridge Hires – Business Card</title>
<link href="https://fonts.googleapis.com/css2?family=Montserrat:wght@400;500;700;800&display=swap" rel="stylesheet">
<style>
  :root {
    --orange: #e0612a;
    --orange-light: #e98a5a;
    --grey-dark: #4f4f51;
    --grey-mid: #7b7b7c;
    --white: #ffffff;
    --page: #e4e4e4;
  }
  * { box-sizing: border-box; margin: 0; padding: 0; }
  html, body { width: 1200px; height: 1200px; overflow: hidden; }
  body {
    background: var(--page);
    font-family: 'Montserrat', sans-serif;
    display: flex;
    flex-direction: column;
    align-items: center;
    justify-content: center;
    gap: 64px;
  }
  .card {
    width: 760px;
    height: 434px;
    border-radius: 26px;
    position: relative;
    overflow: hidden;
    box-shadow: 0 6px 18px rgba(0,0,0,0.18);
  }

  /* Front */
  .card-front {
    background: var(--white);
    display: flex;
    align-items: center;
    justify-content: center;
    gap: 22px;
  }
  .brand-dot {
    flex: none;
    width: 34px; height: 34px;
    border-radius: 50%;
    background: var(--orange);
  }
  .brand-name {
    font-weight: 800;
    font-size: 54px;
    letter-spacing: 2px;
    color: var(--orange);
    line-height: 1.1;
  }

  /* Back */
  .card-back {
    background: linear-gradient(100deg, var(--grey-mid) 0%, var(--grey-dark) 45%, var(--grey-dark) 100%);
    color: var(--white);
  }
  .person {
    position: absolute;
    left: 64px; top: 54px;
  }
  .person-name { font-weight: 700; font-size: 34px; }
  .person-title { font-weight: 400; font-size: 19px; margin-top: 6px; margin-left: 14px; }

  .contact {
    position: absolute;
    left: 78px; top: 176px;
    font-size: 17px;
    line-height: 1.35;
  }
  .address { margin-bottom: 10px; }
  .contact-row { display: flex; align-items: center; gap: 10px; font-size: 18px; }
  .contact-row svg { width: 16px; height: 16px; flex: none; fill: var(--white); }

  .brand-mark {
    position: absolute;
    right: 64px; top: 100px;
    display: flex;
    align-items: center;
    gap: 16px;
  }
  .brand-mark .brand-dot { width: 30px; height: 30px; }
  .brand-mark .brand-name { font-size: 34px; letter-spacing: 1px; }

  .services-band {
    position: absolute;
    left: 0; right: 0; bottom: 0;
    height: 98px;
    background: linear-gradient(90deg, var(--orange-light) 0%, var(--orange) 35%, var(--orange) 100%);
    display: flex;
    flex-direction: column;
    align-items: center;
    justify-content: center;
    font-size: 18px;
    line-height: 1.45;
    letter-spacing: 0.4px;
  }
</style>
</head>
<body>

  <section class="card card-front">
    <span class="brand-dot"></span>
    <span class="brand-name">FALCRIDGE HIRES</span>
  </section>

  <section class="card card-back">
    <div class="person">
      <p class="person-name">Dwight Penner</p>
      <p class="person-title">CFO</p>
    </div>

    <div class="brand-mark">
      <span class="brand-dot"></span>
      <span class="brand-name">FALCRIDGE<br>HIRES</span>
    </div>

    <div class="contact">
      <p class="address">4187 Larkfield Road<br>Brookhaven Ohio 40518</p>
      <p class="contact-row">
        <svg viewBox="0 0 24 24" aria-hidden="true"><path d="M6.6 10.8a15.1 15.1 0 0 0 6.6 6.6l2.2-2.2a1 1 0 0 1 1-.25 11.4 11.4 0 0 0 3.6.57 1 1 0 0 1 1 1V20a1 1 0 0 1-1 1A17 17 0 0 1 3 4a1 1 0 0 1 1-1h3.5a1 1 0 0 1 1 1c0 1.25.2 2.46.57 3.6a1 1 0 0 1-.25 1z"/></svg>
        555 318-0476
      </p>
      <p class="contact-row">
        <svg viewBox="0 0 24 24" aria-hidden="true"><path d="M2 5h20v14H2zm2 2v.5l8 5 8-5V7l-8 5z"/></svg>
        info@falcridgehires.com
      </p>
      <p class="contact-row">
        <svg viewBox="0 0 24 24" aria-hidden="true"><path d="M12 2a10 10 0 1 0 0 20 10 10 0 0 0 0-20zm1 2.1c1.3.9 2.3 3 2.6 5.9H13zm-2 0V10H8.4c.3-2.9 1.3-5 2.6-5.9zM4.1 12h4.3c.1 3 1.1 5.3 2.6 6.5A8 8 0 0 1 4.1 12zm8.9 6.5c1.5-1.2 2.5-3.5 2.6-6.5h4.3a8 8 0 0 1-6.9 6.5z"/></svg>
        www.falcridgehires.com
      </p>
    </div>

    <div class="services-band">
      <p>Luxury Restroom | Trailers Rental and Sales</p>
      <p>Weddings | Concerts | Charity | Sporting | Corp. Events</p>
    </div>
  </section>

</body>
</html>
```